KRT Project Signage

Need a sign to be displayed in the front of properties currently under Construction or Renovation to advertise our company information. Need it to be Professional and Contemporary. We are a Design/Build Construction Company. Information should include Company Name, email, website, phone number. Attached: Logo and company brochure, also included and inspiration images

```html
<!DOCTYPE html>
<html lang="en">
<head>
<meta charset="utf-8">
<title>KRT Project Signage</title>
<link rel="stylesheet" href="https://fonts.googleapis.com/css2?family=League+Spartan:wght@600;700&family=Montserrat+Alternates:wght@500&display=swap">
<style>
  :root {
    --sign-yellow: #f3ea3f;
    --ink: #231f20;
    --paper: #ffffff;
    --page: #ffffff;
  }
  html, body {
    margin: 0;
    padding: 0;
    width: 1200px;
    height: 2864px;
    overflow: hidden;
    background: var(--page);
  }
  .canvas {
    position: relative;
    width: 1200px;
    height: 2864px;
  }
  .project-sign {
    position: absolute;
    left: 80px;
    top: 652px;
    width: 1040px;
    height: 1559px;
    box-shadow: 0 6px 18px rgba(0, 0, 0, 0.18);
    background: var(--paper);
  }
  .project-sign svg { display: block; width: 100%; height: 100%; }
  .headline {
    font-family: "League Spartan", sans-serif;
    font-weight: 700;
    fill: var(--ink);
  }
  .tagline {
    font-family: "League Spartan", sans-serif;
    font-weight: 600;
    fill: var(--ink);
  }
  .phone-number {
    font-family: "League Spartan", sans-serif;
    font-weight: 700;
    fill: var(--paper);
  }
  .contact-line {
    font-family: "Montserrat Alternates", sans-serif;
    font-weight: 500;
    fill: var(--ink);
  }
  .company-name {
    font-family: "League Spartan", sans-serif;
    font-weight: 600;
    fill: var(--ink);
  }
</style>
</head>
<body>
<main class="canvas">
  <section class="project-sign" aria-label="KRT project sign">
    <svg viewBox="0 0 797 1195" xmlns="http://www.w3.org/2000/svg">
      <rect class="sign-base" width="797" height="1195" fill="var(--paper)"/>
      <path class="header-panel" d="M0 0 H797 V600 C700 700 560 740 400 740 C230 740 90 680 0 565 Z" fill="var(--sign-yellow)"/>
      <path class="header-swoosh" d="M90 668 C200 742 320 778 430 778 C600 778 720 712 797 642 V598 C700 702 560 745 400 745 C280 745 170 718 90 668 Z" fill="var(--ink)"/>

      <text class="headline" x="400" y="177" font-size="150" text-anchor="middle" textLength="584" lengthAdjust="spacingAndGlyphs">DORIAN</text>
      <text class="headline" x="400" y="307" font-size="150" text-anchor="middle" textLength="640" lengthAdjust="spacingAndGlyphs">WHITLOCK</text>
      <text class="tagline" x="400" y="375" font-size="60" text-anchor="middle" textLength="616" lengthAdjust="spacing" letter-spacing="10">DESIGN &amp; BUILDER</text>

      <g class="phone-bar">
        <rect x="60" y="394" width="678" height="100" rx="28" fill="var(--ink)"/>
        <circle cx="134" cy="444" r="25" fill="var(--sign-yellow)"/>
        <path class="phone-icon" d="M124 431 c3-2 6-1 7 2 l3 6 c1 2 0 4-2 5 l-2 1 c1 4 4 7 8 8 l1-2 c1-2 3-3 5-2 l6 3 c3 1 4 4 2 7 c-3 4-8 5-13 3 c-8-3-15-10-18-18 c-2-5-1-10 3-13 Z" fill="var(--ink)"/>
        <text class="phone-number" x="432" y="477" font-size="108" text-anchor="middle" textLength="495" lengthAdjust="spacingAndGlyphs">555.210.4187</text>
      </g>

      <g class="contact-email">
        <circle cx="78" cy="538" r="13" fill="var(--paper)"/>
        <path d="M71 533 h14 v10 h-14 Z M71 533 l7 6 l7-6" fill="none" stroke="var(--sign-yellow)" stroke-width="2"/>
        <text class="contact-line" x="107" y="552" font-size="50" textLength="614" lengthAdjust="spacingAndGlyphs">info@krtconstruction.com</text>
      </g>
      <g class="contact-web">
        <circle cx="78" cy="600" r="13" fill="var(--paper)"/>
        <circle cx="78" cy="600" r="7" fill="none" stroke="var(--sign-yellow)" stroke-width="2"/>
        <path d="M71 600 h14 M78 593 v14" stroke="var(--sign-yellow)" stroke-width="2"/>
        <text class="contact-line" x="109" y="612" font-size="50" textLength="598" lengthAdjust="spacingAndGlyphs">www.krtconstruction.com</text>
      </g>

      <g class="company-mark">
        <text class="company-name" x="113" y="992" font-size="72" textLength="532" lengthAdjust="spacingAndGlyphs">KRT CONSTRUCTION</text>
        <circle cx="690" cy="968" r="24" fill="var(--sign-yellow)"/>
      </g>
    </svg>
  </section>
</main>
</body>
</html>
```